Velk Partners Building Business Cards

We need a business card that reflects our business as "Solar Experts" in San Diego. Browse our website www.velkpartners.example our License needs to be displayed as "CSLB# 3867140" our phone number is (619) 555-0187

Save thousands on your electric bills and increase the value of your home while helping to protect the environment. Our solar installation experts will help you design the system that's right for you, using only the highest quality equipment that will look great and give you ideal performance. Our goal is to make you energy independent, and get your electric bill to 0.

Paul Osterby
(619) 555-0187
paul@velkpartners.example

Target Market(s)

Home owners in san diego looking for solar

Industry/Entity Type

Solar Energy

Contact Information for Business Card

Paul Osterby
(619) 555-0187
paul@velkpartners.example

Font styles to use
Other font styles liked:
• Use our logo font

Requirements
Must have
• License needs to be displayed as "CSLB# 3867140" our phone number is (619) 555-0187
Nice to have
• Real images of rooftop home solar in san diego
Should not have
• our business address

```html
<!DOCTYPE html>
<html lang="en">
<head>
<meta charset="utf-8">
<title>Velk Partners Building – Business Card</title>
<link rel="stylesheet" href="https://fonts.googleapis.com/css2?family=Roboto:wght@400;500;700&display=swap">
<style>
  :root {
    --page-bg: #e7e3de;
    --card-bg: #f5f4f2;
    --card-edge: #dcd9d4;
    --navy: #22396a;
    --sun: #eeaa1c;
    --text-muted: #4a5570;
    --band-text: #d9deea;
    --divider: #d2cfca;
  }
  html, body {
    margin: 0;
    padding: 0;
    width: 1200px;
    height: 1200px;
    overflow: hidden;
    background: var(--page-bg);
  }
  .canvas {
    position: relative;
    width: 1200px;
    height: 1200px;
  }
  .business-card {
    position: absolute;
    left: 170px;
    top: 370px;
    width: 860px;
    height: 510px;
    background: var(--card-bg);
    border: 1px solid var(--card-edge);
    box-shadow: 0 14px 40px rgba(60, 50, 40, 0.18);
    overflow: hidden;
    box-sizing: border-box;
  }
  .business-card svg {
    display: block;
    width: 100%;
    height: 100%;
    font-family: "Roboto", Arial, sans-serif;
  }
  .brand-name { fill: var(--navy); font-weight: 700; font-size: 25px; }
  .brand-dot { fill: var(--sun); }
  .divider { stroke: var(--divider); stroke-width: 1; }
  .person-name { fill: var(--navy); font-weight: 700; font-size: 28px; }
  .person-title { fill: var(--text-muted); font-weight: 400; font-size: 18px; }
  .contact-text { fill: var(--navy); font-weight: 400; font-size: 20px; }
  .contact-accent { fill: var(--sun); }
  .contact-icon { fill: var(--sun); }
  .band-yellow { fill: var(--sun); }
  .band-navy { fill: var(--navy); }
  .license-text { fill: var(--band-text); font-weight: 400; font-size: 20px; }
</style>
</head>
<body>
<main class="canvas">
  <section class="business-card" aria-label="Business card for Paul Osterby, Velk Partners Building">
    <svg viewBox="0 0 860 510" xmlns="http://www.w3.org/2000/svg">
      <g class="brand">
        <circle class="brand-dot" cx="62" cy="230" r="18"/>
        <text class="brand-name" x="92" y="239">Velk Partners Building</text>
      </g>

      <line class="divider" x1="405" y1="100" x2="405" y2="355"/>

      <text class="person-name" x="484" y="160">Paul Osterby</text>
      <text class="person-title" x="484" y="190">Managing Director</text>

      <g class="contacts">
        <g class="contact-icon" transform="translate(484 240)">
          <path d="M2 5 Q10 0 18 5 L16 8 Q10 5 4 8 Z"/>
          <rect x="4" y="8" width="12" height="8" rx="1.5"/>
        </g>
        <text class="contact-text" x="526" y="256">(619) 555-0187</text>

        <g transform="translate(494 279)" fill="none" stroke="var(--sun)" stroke-width="1.8">
          <circle r="8.5"/>
          <ellipse rx="3.8" ry="8.5"/>
          <line x1="-8.5" y1="0" x2="8.5" y2="0"/>
        </g>
        <text class="contact-text" x="526" y="286">paul@velkpartners.example</text>

        <g transform="translate(484 302)">
          <rect class="contact-icon" x="0" y="0" width="20" height="14" rx="1"/>
          <path d="M1 1 L10 8 L19 1" fill="none" stroke="var(--card-bg)" stroke-width="1.6"/>
        </g>
        <text class="contact-text" x="526" y="316">www.<tspan class="contact-accent">velkpartners</tspan>.example</text>
      </g>

      <polygon class="band-yellow" points="0,478 432,478 412,510 0,510"/>
      <polygon class="band-navy" points="450,445 860,445 860,510 405,510"/>
      <text class="license-text" x="484" y="484">License: CSLB# 3867140</text>
    </svg>
  </section>
</main>
</body>
</html>
```